Basic business card

use my newly created logo - and the phrases (Lower Cost of Test & Accelarated New Product Introduction) - and my new email domain / ID - use at conferences / tradeshows

Industry/Entity Type

semiconductor

Contact Information for Business Card

Daniel K Forde, Owner, communicate via Logo - Lower COT - Cost of Test, Accelerated NPI - New Product Introduction, phone +1 555 613 0946, Chandler, Arizona, USA, daniel.forde@qal-vub.com

Font styles to use
Sans Serif

Requirements
Nice to have
• re-use my logo created via Pixel Harbor last August (#7315926)

```html
<!DOCTYPE html>
<html lang="en">
<head>
<meta charset="utf-8">
<title>QAL-VUB Business Card</title>
<link rel="stylesheet" href="https://fonts.googleapis.com/css2?family=Montserrat:wght@700&family=Open+Sans:wght@400&display=swap">
<style>
  :root {
    --backdrop: #232323;
    --card: #141414;
    --card-back: #161616;
    --logo-ink: #4d5872;
    --blue: #1677c4;
    --orange: #f5961f;
    --text: #ffffff;
  }
  * { margin: 0; padding: 0; box-sizing: border-box; }
  html, body {
    width: 1200px; height: 780px; overflow: hidden;
    background: var(--backdrop);
    font-family: "Open Sans", sans-serif;
  }
  .stage {
    width: 1200px; height: 780px;
    display: flex; align-items: center; justify-content: center; gap: 40px;
  }
  .card {
    position: relative; width: 540px; height: 309px; overflow: hidden;
    background: var(--card);
    box-shadow: 0 10px 30px rgba(0,0,0,.45);
  }
  .card-back { background: var(--card-back); }
  .back-pattern { position: absolute; inset: 0;
    background: linear-gradient(135deg, #1c1c1c, #121212); }

  .brand {
    position: absolute; left: 40px; top: 140px;
    display: flex; align-items: center; gap: 12px;
  }
  .brand-square { width: 34px; height: 34px; background: var(--logo-ink); }
  .brand-name {
    font-family: "Open Sans", sans-serif; font-size: 38px; font-weight: 400;
    color: var(--logo-ink); letter-spacing: 1px;
  }
  .divider {
    position: absolute; left: 296px; top: 88px; width: 1px; height: 148px;
    background: var(--blue);
  }
  .contact { position: absolute; left: 316px; top: 62px; color: var(--text); }
  .person-name { font-family: "Montserrat", sans-serif; font-weight: 700; font-size: 20px; line-height: 1.1; }
  .person-name .first { color: var(--blue); }
  .person-name .last { color: var(--orange); }
  .person-role { font-size: 11px; margin-top: 2px; }
  .details { list-style: none; margin-top: 14px; font-size: 11px; line-height: 1.55; }
  .details li { display: flex; align-items: center; gap: 7px; }
  .details svg { width: 10px; height: 10px; fill: var(--blue); flex: none; }
  .address { margin-top: 12px; font-size: 11px; line-height: 1.5; }
  .waves { position: absolute; left: 0; top: 0; width: 540px; height: 309px; }
</style>
</head>
<body>
<main class="stage">
  <section class="card card-back">
    <div class="back-pattern" role="img" aria-label="Repeating embossed brand symbol pattern in dark grey"></div>
  </section>

  <section class="card card-front">
    <div class="brand">
      <span class="brand-square"></span>
      <span class="brand-name">QAL-VUB</span>
    </div>

    <div class="divider"></div>

    <div class="contact">
      <h1 class="person-name"><span class="first">Theo</span> <span class="last">Varga</span></h1>
      <p class="person-role">Managing Director</p>
      <ul class="details">
        <li><svg viewBox="0 0 10 10"><path d="M2 0h2l1 3-1.5 1a6 6 0 0 0 2.5 2.5L7 5l3 1v2c0 1-1 2-2 2A8 8 0 0 1 0 2c0-1 1-2 2-2z"/></svg>123 456 789</li>
        <li><svg viewBox="0 0 10 10"><path d="M0 2h10v6H0z M0 2l5 3.5L10 2" stroke="#141414" stroke-width=".8"/></svg>info@yourmail.com</li>
        <li><svg viewBox="0 0 10 10"><circle cx="5" cy="5" r="5"/><path d="M0 5h10M5 0v10" stroke="#141414" stroke-width=".7"/></svg>www.yourwebsite.com</li>
      </ul>
      <p class="address">Your address, City<br>State, Zip 1234</p>
    </div>

    <svg class="waves" viewBox="0 0 540 309" aria-hidden="true">
      <path d="M0 278 C160 274 300 252 400 240 C450 234 480 232 520 230 L520 232 C470 236 440 242 400 250 C300 270 160 290 0 286 Z" fill="var(--orange)"/>
      <path d="M0 309 L0 296 C160 298 300 270 410 252 C460 244 500 238 530 236 L540 236 L540 309 Z" fill="var(--blue)"/>
    </svg>
  </section>
</main>
</body>
</html>
```